KAJU Freightways #ALLKAJU Business Cards & Letterhead

I am looking to business cards designed for our organization. We are currently undergoing a small re-branding that is taking place. Our organization is called KAJU Freightways and we are headquartered in Phoenix, AZ. We primarily provide transportation and logistics services to the Marlow Parcel Bureau who is our largest customer. I would like to see a design that incorporates name, title, contact info, website, and address (this will be different depending on the employee). I would also like to see some color on the business card using our logo colors or a variation. I would like our logo on the back of the business card with the website displayed. The final design should communicate that we are a next generation transportation operate that focuses on being driver-first, customer-centric, innovative, and sustainable.We would also like our #ALLKAJU catch phrase incorporated as well.

Target Market(s)

Transportation & Logistics

Industry/Entity Type

Trucking Company

Contact Information for Business Card

-First and Last Name
-Position Title
-Contact Phone
-Contact Email
-Physical Address

Font styles to use
Serif

Colors

Designer to choose colors to be used in the design.

Requirements
Must have
• -KAJU logo prominently displayed
• -#ALLKAJU catch phrase used
• -Some amount of color, design gradient, etc.
• -Logo on the back with website listed (https://www.kajufreightco.example)

```html
<!DOCTYPE html>
<html lang="en">
<head>
<meta charset="utf-8">
<title>KAJU Freightways Business Card</title>
<link rel="stylesheet" href="https://fonts.googleapis.com/css2?family=Tinos:wght@400;700&display=swap">
<style>
  :root {
    --page-bg: #ececec;
    --brand-green: #84c442;
    --brand-navy: #053a47;
    --card-white: #ffffff;
    --text-grey: #3a3a3a;
  }
  html, body {
    margin: 0;
    padding: 0;
    width: 1200px;
    height: 1020px;
    overflow: hidden;
    background: var(--page-bg);
    font-family: "Tinos", "Times New Roman", serif;
  }
  .canvas {
    position: relative;
    width: 1200px;
    height: 1020px;
  }
  .card {
    position: absolute;
    left: 272px;
    width: 656px;
    height: 376px;
    border-radius: 20px;
    overflow: hidden;
  }
  .card--front {
    top: 88px;
    background: var(--brand-green);
  }
  .card--back {
    top: 514px;
    background: var(--card-white);
  }
  .front-mark {
    position: absolute;
    inset: 0;
    display: flex;
    flex-direction: column;
    align-items: center;
    justify-content: center;
  }
  .front-mark__row {
    display: flex;
    align-items: center;
    gap: 16px;
  }
  .front-mark__dot {
    width: 22px;
    height: 22px;
    border-radius: 50%;
    background: var(--card-white);
  }
  .front-mark__name {
    font-weight: 700;
    font-size: 84px;
    line-height: 1;
    color: var(--card-white);
    letter-spacing: 2px;
  }
  .front-mark__tag {
    margin: 22px 0 0;
    font-size: 22px;
    font-weight: 700;
    line-height: 1;
    color: var(--card-white);
    letter-spacing: 3px;
  }
  .front-mark__web {
    margin: 10px 0 0;
    font-size: 18px;
    line-height: 1;
    color: var(--card-white);
    letter-spacing: 0.5px;
  }
  .back-mark {
    position: absolute;
    left: 40px;
    top: 159px;
    width: 280px;
    display: flex;
    align-items: center;
    gap: 12px;
  }
  .back-mark__dot {
    width: 22px;
    height: 22px;
    border-radius: 50%;
    background: var(--brand-green);
  }
  .back-mark__name {
    font-weight: 700;
    font-size: 64px;
    line-height: 1;
    color: var(--brand-navy);
    letter-spacing: 1px;
  }
  .divider {
    position: absolute;
    left: 326px;
    top: 98px;
    width: 2px;
    height: 182px;
    background: var(--brand-green);
  }
  .details {
    position: absolute;
    left: 343px;
    top: 95px;
    color: var(--text-grey);
  }
  .details__name {
    margin: 0;
    font-size: 25px;
    font-weight: 700;
    color: var(--brand-green);
    line-height: 28px;
    letter-spacing: 0.5px;
  }
  .details__title {
    margin: 0;
    font-size: 18px;
    line-height: 22px;
  }
  .details__address {
    margin: 13px 0 0;
    font-size: 17px;
    line-height: 23px;
    font-style: normal;
  }
  .contact-list {
    list-style: none;
    margin: 10px 0 0;
    padding: 0;
    font-size: 17px;
    line-height: 22px;
  }
  .contact-list li {
    display: flex;
    align-items: center;
    gap: 8px;
  }
  .contact-list svg {
    width: 13px;
    height: 13px;
    flex: none;
  }
</style>
</head>
<body>
<main class="canvas">
  <section class="card card--front" aria-label="Card front">
    <div class="front-mark">
      <div class="front-mark__row">
        <span class="front-mark__dot"></span>
        <span class="front-mark__name">KAJU</span>
      </div>
      <p class="front-mark__tag">#ALLKAJU</p>
      <p class="front-mark__web">www.kajufreightco.example</p>
    </div>
  </section>

  <section class="card card--back" aria-label="Card back">
    <div class="back-mark">
      <span class="back-mark__dot"></span>
      <span class="back-mark__name">KAJU</span>
    </div>
    <div class="divider"></div>
    <div class="details">
      <h1 class="details__name">Dana Reyes</h1>
      <p class="details__title">Owner</p>
      <address class="details__address">418 Juniper Road,<br>Phoenix AZ 85004</address>
      <ul class="contact-list">
        <li>
          <svg viewBox="0 0 16 16" aria-hidden="true"><path fill="#84c442" d="M3.5 1.5l2.5 3-1.5 1.6c.8 1.9 2.3 3.4 4.2 4.2l1.6-1.5 3 2.5-1.4 2.4C7 13.4 2.6 9 1.3 3z"/></svg>
          <span>(602) 555-0148</span>
        </li>
        <li>
          <svg viewBox="0 0 16 16" aria-hidden="true"><rect x="1" y="3" width="14" height="10" fill="#84c442"/><path d="M1.5 3.5L8 9l6.5-5.5" fill="none" stroke="#fff" stroke-width="1.3"/></svg>
          <span>dana@kajufreight.example</span>
        </li>
        <li>
          <svg viewBox="0 0 16 16" aria-hidden="true"><circle cx="8" cy="8" r="7" fill="#84c442"/><path d="M1 8h14M8 1c-3 3.5-3 10.5 0 14M8 1c3 3.5 3 10.5 0 14" fill="none" stroke="#fff" stroke-width="1"/></svg>
          <span>www.kajufreightco.example</span>
        </li>
      </ul>
    </div>
  </section>
</main>
</body>
</html>
```